Consulting company business cards

We have a base design, but would be willing to update. We have a new logo/"tag" that needs to be added. Current business card design is attached for reference into our "style."

Industry/Entity Type

Business

Contact Information for Business Card

Should contain name and title, office number, mobile number if appropriate, e-mail, website, physical address, and company logo.

Font styles to use
Other font styles liked:
• See current card design on KorvandBCard

Colors
0455a3
85acd3
aaaaaa

Requirements
Must have
• Our colors are navy blue, gray, and a lighter blue
Nice to have
• Design that I can easily drop in new names/titles as we hire employees.

```html
<!DOCTYPE html>
<html lang="en">
<head>
<meta charset="utf-8">
<title>Mossbury Business Cards</title>
<link href="https://fonts.googleapis.com/css2?family=Source+Sans+3:wght@400;600&display=swap" rel="stylesheet">
<style>
  :root {
    --stage: #474747;
    --navy: #002d4e;
    --navy-ink: #0b3556;
    --sky: #7eafcf;
    --sky-deep: #6f9fc1;
    --sky-soft: #a9c9df;
    --white: #ffffff;
  }
  * { margin: 0; padding: 0; box-sizing: border-box; }
  html, body {
    width: 1200px; height: 900px; overflow: hidden;
    background: var(--stage);
    font-family: "Source Sans 3", sans-serif;
  }
  .stage { position: relative; width: 1200px; height: 900px; }
  .card {
    position: absolute; top: 306px;
    width: 440px; height: 271px; border-radius: 10px;
    overflow: hidden;
  }
  .card--front { left: 149px; background: var(--navy); color: var(--white); }
  .card--back { left: 608px; background: var(--sky); }

  .back-decoration {
    position: absolute; left: 180px; top: 0; width: 260px; height: 271px;
    background: radial-gradient(ellipse at 70% 45%, var(--sky-deep) 0%, rgba(111,159,193,0) 70%);
  }

  .brand { position: absolute; display: flex; flex-direction: column; }
  .brand__row { display: flex; align-items: center; gap: 10px; }
  .brand__name { font-weight: 600; line-height: 1; letter-spacing: 0.5px; white-space: nowrap; }
  .brand__mark { border-radius: 3px; }
  .brand__tag { letter-spacing: 1.6px; white-space: nowrap; }

  .card--front .brand { right: 26px; top: 36px; align-items: flex-end; }
  .card--front .brand__name { font-size: 40px; color: var(--white); }
  .card--front .brand__mark { width: 22px; height: 22px; background: var(--sky); }
  .card--front .brand__tag { font-size: 11px; color: var(--sky-soft); margin-top: 6px; }

  .card--back .brand { left: 102px; top: 102px; align-items: flex-start; }
  .card--back .brand__name { font-size: 46px; color: var(--navy-ink); }
  .card--back .brand__mark { width: 26px; height: 26px; background: var(--white); }
  .card--back .brand__tag { font-size: 12px; color: var(--white); margin-top: 8px; }

  .person { position: absolute; left: 29px; top: 119px; }
  .person__name { font-size: 17px; font-weight: 600; line-height: 20px; }
  .person__title { font-size: 13px; line-height: 16px; margin-top: 6px; }
  .divider {
    position: absolute; left: 0; right: 0; top: 140px;
    height: 1.5px; background: var(--white);
  }

  .contact {
    position: absolute; right: 26px; top: 152px;
    list-style: none; text-align: right; font-size: 13px;
  }
  .contact li { display: flex; justify-content: flex-end; align-items: center; gap: 8px; height: 18px; }
  .contact svg { width: 10px; height: 10px; fill: var(--white); }
  .contact__address { margin-top: 2px; }
</style>
</head>
<body>
<main class="stage">

  <section class="card card--front" aria-label="Business card front">
    <div class="brand">
      <div class="brand__row">
        <span class="brand__name">MOSSBURY</span>
        <span class="brand__mark" aria-hidden="true"></span>
      </div>
      <span class="brand__tag">CLOUD TECHNOLOGY ADVISORS</span>
    </div>

    <div class="person">
      <p class="person__name">Dana Korvand</p>
      <p class="person__title">Office Manager</p>
    </div>
    <div class="divider"></div>

    <ul class="contact">
      <li>555.204.3810
        <svg viewBox="0 0 10 10" aria-label="Phone"><path d="M2 .5l1.6 1.9-.9 1.2c.6 1.3 1.5 2.2 2.8 2.8l1.2-.9L8.6 7 7.7 9C4.1 8.7 1.3 5.9 1 2.3z"/></svg>
      </li>
      <li>555.204.3871
        <svg viewBox="0 0 10 10" aria-label="Fax"><path d="M2.5 1h5v2.5h-5zM1 4h8v4H7.5V6.5h-5V8H1zM3 7h4v2.5H3z"/></svg>
      </li>
      <li>dkorvand@mossburytech.com
        <svg viewBox="0 0 10 10" aria-label="Email"><path d="M.5 2h9v6h-9zM1.3 2.6L5 5.4l3.7-2.8" stroke="#002d4e" stroke-width=".8"/></svg>
      </li>
      <li>mossburytech.com
        <svg viewBox="0 0 10 10" aria-label="Website"><circle cx="5" cy="5" r="4.5"/><path d="M.5 5h9M5 .5c-2 2.5-2 6.5 0 9M5 .5c2 2.5 2 6.5 0 9" fill="none" stroke="#002d4e" stroke-width=".7"/></svg>
      </li>
      <li class="contact__address">1870 W 58TH St Carmel Indiana 46032</li>
    </ul>
  </section>

  <section class="card card--back" aria-label="Business card back">
    <div class="back-decoration" role="img" aria-label="Faint large brand decoration in a deeper sky tone"></div>
    <div class="brand">
      <div class="brand__row">
        <span class="brand__name">MOSSBURY</span>
        <span class="brand__mark" aria-hidden="true"></span>
      </div>
      <span class="brand__tag">CLOUD TECHNOLOGY ADVISORS</span>
    </div>
  </section>

</main>
</body>
</html>
```